Flat bootstrap design for existing site

I'm looking for a modern flat design based around an existing logo. This has to be a custom design (no external templates), and implemented into a bootstrap framework.

The logo is attached as 2 versions - choose whichever you want, that flows better with whatever design you choose.

Added screenshots of the existing site (currently using the default bootstrap layouts). Please make your designs around those pages in the screenshots (i.e. the homepage only has the postal code input and the header). The active page has 3 screenshots, because I wanted to illustrate the other states that would be visible (in the table rows).

This is a moving/junk removal website, just for some context.

Here's some example websites (flat designs) that I like, just to give you an idea of what I'm after.

https://www.plimvora.com/
https://dacklow.com/
https://trevanu.com/
https://quobrintal.com/en/

Coding

Coded - Design and coding required

Number of Pages Required

5+ page

Colors

Designer to choose colors to be used in the design.

Requirements
Must have
• It must be a modern/simple flat design, that is built around the existing logo (attached).
• It has to be implemented using bootstrap.

```html
<!DOCTYPE html>
<html lang="en">
<head>
<meta charset="utf-8">
<title>Hauliq — Junk Removal</title>
<link rel="stylesheet" href="https://fonts.googleapis.com/css2?family=Ubuntu:wght@400;500;700&family=Poppins:wght@500&family=Merriweather:wght@900&display=swap">
<style>
  :root {
    --sky: #4bc9f5;
    --sky-deep: #29a9d6;
    --sky-edge: #36b6e4;
    --ink: #666666;
    --field-line: #7a7a7a;
    --placeholder: #8a8a8a;
    --white: #ffffff;
  }
  * { box-sizing: border-box; margin: 0; padding: 0; }
  html, body {
    width: 1200px;
    height: 434px;
    overflow: hidden;
    background: var(--white);
  }
  .page {
    position: relative;
    width: 1200px;
    height: 434px;
  }
  .site-header {
    position: absolute;
    top: 0; left: 0;
    width: 100%;
    height: 47px;
    background: var(--sky);
  }
  .brand {
    position: absolute;
    left: 99px;
    top: 0;
    height: 47px;
    display: flex;
    align-items: center;
    font-family: "Ubuntu", sans-serif;
    font-weight: 700;
    font-size: 22px;
    letter-spacing: 0.5px;
    color: var(--white);
    text-decoration: none;
  }
  .main-nav {
    position: absolute;
    top: 0;
    right: 0;
    height: 47px;
    display: flex;
  }
  .nav-link {
    display: flex;
    align-items: center;
    height: 47px;
    font-family: "Ubuntu", sans-serif;
    font-weight: 500;
    font-size: 14px;
    color: var(--white);
    text-decoration: none;
    position: absolute;
    top: 0;
    white-space: nowrap;
  }
  .nav-link--book { left: -480px; }
  .nav-link--how { left: -411px; }
  .nav-link--driver {
    left: -303px;
    width: 136px;
    justify-content: center;
    background: var(--sky-deep);
  }
  .nav-link--signin { left: -145px; }

  .hero {
    position: absolute;
    top: 0; left: 0;
    width: 100%;
  }
  .hero-title {
    position: absolute;
    top: 180px;
    left: 0;
    width: 100%;
    padding-left: 15px;
    text-align: center;
    font-family: "Ubuntu", sans-serif;
    font-weight: 400;
    font-size: 29px;
    color: var(--ink);
  }
  .postal-form {
    position: absolute;
    top: 243px;
    left: 423px;
    display: flex;
    gap: 12px;
  }
  .postal-input {
    width: 263px;
    height: 28px;
    border: 1px solid var(--field-line);
    padding: 0 8px;
    font-family: "Ubuntu", sans-serif;
    font-size: 10px;
    color: var(--ink);
    background: var(--white);
  }
  .postal-input::placeholder { color: var(--placeholder); }
  .book-button {
    width: 112px;
    height: 28px;
    border: 1px solid var(--sky-edge);
    border-radius: 14px;
    background: var(--sky);
    color: var(--white);
    font-family: "Merriweather", serif;
    font-weight: 900;
    font-size: 12px;
    letter-spacing: 0.5px;
  }

  .site-footer {
    position: absolute;
    left: 0;
    top: 404px;
    width: 100%;
    height: 30px;
    background: var(--sky);
    display: flex;
    align-items: center;
    justify-content: center;
    font-family: "Poppins", sans-serif;
    font-weight: 500;
    font-size: 11px;
    color: var(--white);
  }
</style>
</head>
<body>
<div class="page">
  <header class="site-header">
    <a class="brand" href="#">HAULIQ</a>
    <nav class="main-nav">
      <a class="nav-link nav-link--book" href="#">Book</a>
      <a class="nav-link nav-link--how" href="#">How It Works</a>
      <a class="nav-link nav-link--driver" href="#">Become A Driver</a>
      <a class="nav-link nav-link--signin" href="#">Sign In</a>
    </nav>
  </header>

  <main class="hero">
    <h1 class="hero-title">Need Junk Removed? Book Now</h1>
    <form class="postal-form" action="#">
      <input class="postal-input" type="text" placeholder="Postal Code" aria-label="Postal Code">
      <button class="book-button" type="submit">BOOK</button>
    </form>
  </main>

  <footer class="site-footer">© 2017 Hauliq. All Rights Reserved.</footer>
</div>
</body>
</html>
```